Inspiring Fundraising Foundation Website to Provide Academic Scholarships

Hello, we are launching a foundation to provide academic scholarships to high school students for college. We'd like this to be an informational website with contact information. There will be a total of approximately 5-7 pages in all.
The color scheme will be purple and white, with a girly feel. I 've attached the logo for reference!

Target Market(s)

high school students, college students

Industry/Entity Type

Education

Coding

Coded - Design and coding required

Number of Pages Required

5+ page

Font styles to use
Serif
Sans Serif
Script

Colors
6b449b
886aae
b7a5cd
e4daeb
ffffff
fdf9cf
fbf289

Requirements
Must have
• Purple, girly feel, to reflect the logo's style. Should be light-themed
Should not have
• No dark themes (aka heavy on black or dark colors)

```html
<!DOCTYPE html>
<html lang="en">
<head>
<meta charset="utf-8">
<title>Marisol Avendano Foundation</title>
<link href="https://fonts.googleapis.com/css2?family=Raleway:wght@500;600;700;800&family=Open+Sans:wght@400;600;700&family=Roboto:wght@400;500&display=swap" rel="stylesheet">
<style>
:root{
  --purple-deep:#3f1460;
  --purple:#4b1d6e;
  --purple-mid:#6b449b;
  --purple-soft:#886aae;
  --lilac:#b7a5cd;
  --lilac-pale:#e4daeb;
  --yellow:#fbf289;
  --cream:#fdf9cf;
  --white:#ffffff;
  --ink:#222222;
  --text:#3a3a3a;
  --grey-bar:#e8e8e8;
}
*{margin:0;padding:0;box-sizing:border-box}
html,body{width:1200px;height:2671px;overflow:hidden}
body{position:relative;background:var(--white);font-family:"Open Sans",sans-serif;color:var(--text)}
.abs{position:absolute}

/* header */
.site-header{position:absolute;left:0;top:0;width:1200px;height:125px;background:var(--white);z-index:3}
.brand{position:absolute;left:96px;top:4px;width:188px;height:188px;border-radius:50%;background:var(--white);z-index:4;display:flex;flex-direction:column;align-items:center;justify-content:center;text-align:center;font-family:"Raleway",sans-serif;font-weight:700;color:var(--purple-mid);font-size:22px;line-height:1.1}
.brand small{font-size:13px;letter-spacing:3px;margin-top:6px;font-weight:700}
.topbar{position:absolute;right:32px;top:26px;display:flex;align-items:center;gap:0}
.social-dot{width:32px;height:32px;border:1.5px solid var(--ink);border-radius:50%;margin-right:6px}
.contact-chip{display:flex;align-items:center;margin-left:42px;font-family:"Roboto",sans-serif;font-size:17px;font-weight:500;color:var(--ink)}
.contact-chip .chip-icon{width:32px;height:32px;border-radius:50%;display:flex;align-items:center;justify-content:center;margin-right:10px}
.chip-mail{background:var(--purple)}
.chip-phone{background:#3a3a3a}
.main-nav{position:absolute;right:32px;top:89px;display:flex;gap:28px;font-family:"Roboto",sans-serif;font-size:15px;font-weight:500;color:var(--ink)}
.main-nav .active{color:var(--purple)}

/* hero */
.hero{position:absolute;left:0;top:125px;width:1200px;height:516px;background:linear-gradient(120deg,#6f5a55 0%,#8a4a48 35%,#5f6067 65%,#3f3c40 100%)}
.hero-shade{position:absolute;inset:0;background:linear-gradient(90deg,rgba(0,0,0,.05),rgba(0,0,0,.35))}
.hero-title{position:absolute;right:96px;top:130px;font-family:"Raleway",sans-serif;font-weight:800;font-size:52px;color:var(--white);letter-spacing:1px}
.hero-sub{position:absolute;right:96px;top:212px;width:520px;text-align:right;font-size:15px;line-height:27px;color:var(--white)}
.btn-ghost{position:absolute;left:961px;top:290px;width:139px;height:55px;border:2px solid var(--white);color:var(--white);font-family:"Raleway",sans-serif;font-weight:600;font-size:16px;display:flex;align-items:center;justify-content:center}
.hero-dots{position:absolute;left:1011px;top:381px;display:flex;gap:7px}
.hero-dots span{width:13px;height:13px;border-radius:50%;border:1.5px solid var(--white)}
.hero-dots .on{background:var(--purple-mid)}

/* headings */
.section-title{font-family:"Raleway",sans-serif;font-weight:700;font-size:27px;color:var(--purple)}
.rule{height:2px;background:var(--purple)}
.body-copy{font-size:13px;line-height:24px;color:var(--text)}
.body-copy p+p{margin-top:8px}
.btn-solid{background:var(--purple-deep);color:var(--white);font-family:"Raleway",sans-serif;font-weight:700;font-size:15px;display:flex;align-items:center;justify-content:center}

/* about */
.video-frame{position:absolute;left:698px;top:710px;width:399px;height:281px;border:3px solid #ddd;background:linear-gradient(135deg,#c9a78d,#4d6c96 55%,#e8d3b8);box-shadow:0 28px 30px -18px rgba(0,0,0,.45)}
.video-play{position:absolute;left:168px;top:102px;width:54px;height:54px;border:3px solid var(--white);border-radius:50%;background:rgba(0,0,0,.2)}
.video-play::after{content:"";position:absolute;left:20px;top:14px;border-left:16px solid var(--white);border-top:10px solid transparent;border-bottom:10px solid transparent}
.video-bar{position:absolute;left:0;right:0;bottom:0;height:18px;background:rgba(20,20,30,.8)}
.video-bar i{position:absolute;left:14px;top:7px;width:220px;height:4px;background:var(--lilac)}

/* scholarships */
.scholarships{position:absolute;left:0;top:1072px;width:1200px;height:492px;background:var(--yellow)}
.pin{position:absolute;top:162px;width:140px;height:160px}
.card-title{position:absolute;top:347px;width:210px;text-align:center;font-family:"Roboto",sans-serif;font-weight:500;font-size:16.5px;color:var(--ink)}
.card-text{position:absolute;top:382px;width:196px;text-align:center;font-family:"Roboto",sans-serif;font-size:12.5px;line-height:19px;color:var(--ink)}

/* story */
.portrait{position:absolute;left:99px;top:1661px;width:233px;height:233px;border-radius:50%;border:3px solid var(--purple);padding:5px;background:var(--white)}
.portrait div{width:100%;height:100%;border-radius:50%;background:linear-gradient(160deg,#f2f2f2 0%,#e7e2e0 45%,#b6423a 70%,#9a2f2a 100%)}

/* newsletter band */
.newsletter{position:absolute;left:0;top:2003px;width:1200px;height:266px;background:linear-gradient(100deg,#4e1f72 0%,#5a2a82 50%,#46186a 100%)}
.newsletter h2{position:absolute;left:374px;top:44px;font-family:"Raleway",sans-serif;font-weight:600;font-size:26px;color:var(--white)}
.newsletter p{position:absolute;left:374px;top:95px;width:730px;font-size:13px;line-height:24px;color:var(--lilac-pale)}
.email-field{position:absolute;left:376px;top:174px;width:377px;height:45px;border-radius:5px;background:rgba(228,218,235,.75);font-family:"Roboto",sans-serif;font-size:15px;color:#4a3a5a;display:flex;align-items:center;padding-left:14px}
.btn-subscribe{position:absolute;left:771px;top:174px;width:169px;height:45px;border:2px solid var(--white);color:var(--white);font-family:"Roboto",sans-serif;font-weight:500;font-size:15px;display:flex;align-items:center;justify-content:center}

/* footer */
.site-footer{position:absolute;left:0;top:2269px;width:1200px;height:340px;background:var(--white)}
.footer-map{position:absolute;inset:0;background:linear-gradient(120deg,#eef0ec 0%,#f5f5f2 50%,#e9edf0 100%);opacity:.9}
.footer-brand{position:absolute;left:100px;top:110px;width:150px;text-align:center;font-family:"Raleway",sans-serif;font-weight:700;font-size:24px;line-height:1.1;color:var(--purple-mid)}
.footer-brand small{display:block;font-size:13px;letter-spacing:3px;margin-top:6px}
.footer-col h3{font-family:"Raleway",sans-serif;font-weight:700;font-size:17px;color:var(--purple)}
.footer-col .rule{width:110px;margin-top:9px;height:2px}
.quick-links{list-style:none;margin-top:20px;font-family:"Roboto",sans-serif;font-size:15px;color:var(--ink)}
.quick-links li{height:31.7px}
.contact-row{position:absolute;left:0;display:flex}
.contact-icon{width:38px;height:38px;border:2px solid var(--purple);border-radius:50%;display:flex;align-items:center;justify-content:center;margin-right:16px;flex:none}
.contact-row .label{font-family:"Roboto",sans-serif;font-weight:500;font-size:13.5px;color:var(--ink)}
.contact-row .value{font-family:"Roboto",sans-serif;font-size:12.5px;line-height:20px;color:var(--ink)}
.form-field{position:absolute;border:1.5px solid #8d8d8d;background:var(--white);font-family:"Roboto",sans-serif;font-size:11px;color:#333;padding:8px 8px}
.bottom-bar{position:absolute;left:0;top:2609px;width:1200px;height:62px;background:var(--grey-bar)}
.copyright{position:absolute;left:100px;top:22px;font-family:"Roboto",sans-serif;font-weight:500;font-size:14px;color:var(--ink)}
.bottom-social{position:absolute;left:872px;top:11px;display:flex;gap:10px}
.bottom-social span{width:40px;height:40px;border-radius:50%;border:2px solid var(--ink)}
</style>
</head>
<body>

<header class="site-header">
  <div class="topbar">
    <span class="social-dot"></span><span class="social-dot"></span><span class="social-dot"></span><span class="social-dot"></span>
    <span class="contact-chip"><span class="chip-icon chip-mail"><svg width="16" height="12" viewBox="0 0 16 12"><rect x="1" y="1" width="14" height="10" fill="none" stroke="#fff" stroke-width="1.5"/><path d="M1 1l7 6 7-6" fill="none" stroke="#fff" stroke-width="1.5"/></svg></span>info@marisolavendano.org</span>
    <span class="contact-chip"><span class="chip-icon chip-phone"><svg width="16" height="16" viewBox="0 0 24 24"><path d="M6.6 10.8a15 15 0 006.6 6.6l2.2-2.2c.3-.3.7-.4 1-.2 1.1.4 2.3.6 3.6.6.6 0 1 .4 1 1V20c0 .6-.4 1-1 1A17 17 0 013 4c0-.6.4-1 1-1h3.5c.6 0 1 .4 1 1 0 1.3.2 2.5.6 3.6.1.3 0 .7-.2 1z" fill="#fff"/></svg></span>180 041 7720</span>
  </div>
  <nav class="main-nav">
    <span class="active">HOME</span><span>COURSES</span><span>FEATURES</span><span>EVENTS</span><span>SCHOLARSHIPS</span><span>BLOG</span><span>CONTACT</span>
  </nav>
</header>
<div class="brand">Marisol<br>Avendano<small>FOUNDATION</small></div>

<section class="hero">
  <div class="abs" style="inset:0" role="img" aria-label="Photo of young children working at desks in a bright classroom"></div>
  <div class="hero-shade"></div>
  <h1 class="hero-title">MARISOL AVENDANO</h1>
  <p class="hero-sub">Duis aute irure dolor in reprehenderit in voluptate velit esse cillum dolore eu fugiat nulla pariatur.</p>
  <span class="btn-ghost">Read More</span>
  <div class="hero-dots"><span class="on"></span><span></span><span></span><span></span><span></span></div>
</section>

<section class="about">
  <h2 class="section-title abs" style="left:100px;top:703px">About Marisol Avendano Foundation</h2>
  <div class="rule abs" style="left:100px;top:744px;width:265px"></div>
  <div class="body-copy abs" style="left:100px;top:764px;width:536px">
    <p>The Marisol Avendano Foundation is dedicated to helping Bayfield young men and women reach their goal of starting a real estate career. Our foundation will work to make a difference by offering scholarships and internships for future agents.</p>
    <p>The foundation will award scholarships to two hard working juniors or seniors in college per year. To be eligible, applicants must send their resume and a 1-2 page essay stating why they are passionate in real estate and what they hope to achieve. Application will open February 20th, 2017 and close May 1st, 2017.</p>
  </div>
  <span class="btn-solid abs" style="left:100px;top:960px;width:112px;height:41px">Read More</span>
  <div class="video-frame" role="img" aria-label="Video still of schoolchildren drawing together at a table">
    <span class="video-play"></span>
    <span class="video-bar"><i></i></span>
  </div>
</section>

<section class="scholarships">
  <h2 class="section-title abs" style="left:0;width:1200px;text-align:center;top:50px">Our Scholarships</h2>
  <div class="rule abs" style="left:555px;top:101px;width:90px"></div>

  <svg class="pin" style="left:133px" viewBox="0 0 140 160"><path d="M70 4a66 66 0 0 1 18 129.5L70 152 52 133.5A66 66 0 0 1 70 4z" fill="none" stroke="#3f1460" stroke-width="3"/><g fill="#3f1460"><circle cx="52" cy="58" r="9"/><circle cx="88" cy="58" r="9"/><circle cx="70" cy="52" r="11"/><path d="M36 86c0-12 8-18 16-18s16 6 16 18zM72 86c0-12 8-18 16-18s16 6 16 18z"/><path d="M52 90c0-16 8-24 18-24s18 8 18 24z"/></g></svg>
  <svg class="pin" style="left:330px" viewBox="0 0 140 160"><path d="M70 4a66 66 0 0 1 18 129.5L70 152 52 133.5A66 66 0 0 1 70 4z" fill="#4b1d6e"/><g fill="#fff"><circle cx="74" cy="50" r="13"/><path d="M48 102c0-22 12-32 26-32s26 10 26 32z"/><rect x="44" y="44" width="3" height="44" transform="rotate(-30 46 66)"/></g></svg>
  <svg class="pin" style="left:539px" viewBox="0 0 140 160"><path d="M70 4a66 66 0 0 1 18 129.5L70 152 52 133.5A66 66 0 0 1 70 4z" fill="none" stroke="#3f1460" stroke-width="3"/><g fill="#3f1460"><rect x="56" y="36" width="46" height="32" fill="none" stroke="#3f1460" stroke-width="4"/><circle cx="50" cy="62" r="9"/><path d="M38 92c0-12 5-18 12-18s12 6 12 18z"/><circle cx="72" cy="86" r="7"/><circle cx="92" cy="86" r="7"/></g></svg>
  <svg class="pin" style="left:747px" viewBox="0 0 140 160"><path d="M70 4a66 66 0 0 1 18 129.5L70 152 52 133.5A66 66 0 0 1 70 4z" fill="none" stroke="#3f1460" stroke-width="3"/><g fill="#3f1460"><rect x="40" y="40" width="60" height="40" fill="none" stroke="#3f1460" stroke-width="5"/><rect x="64" y="80" width="12" height="10"/><rect x="54" y="90" width="32" height="5"/><path d="M82 60l18-22 6 5-18 22-8 3z"/></g></svg>
  <svg class="pin" style="left:948px" viewBox="0 0 140 160"><path d="M70 4a66 66 0 0 1 18 129.5L70 152 52 133.5A66 66 0 0 1 70 4z" fill="none" stroke="#3f1460" stroke-width="3"/><g fill="#3f1460"><path d="M70 30l24 9-24 9-24-9z"/><circle cx="70" cy="56" r="10"/><path d="M44 100V76l26 8 26-8v24l-26 6z"/></g></svg>

  <h3 class="card-title" style="left:98px">School Students</h3>
  <h3 class="card-title" style="left:295px">Fundraising Foundation</h3>
  <h3 class="card-title" style="left:504px">Academic Scholarships</h3>
  <h3 class="card-title" style="left:712px">School Services</h3>
  <h3 class="card-title" style="left:913px">Expert Consulting</h3>
  <p class="card-text" style="left:105px">Our team at Bright Tutor may be small, but it's the exact size we need to make sure.</p>
  <p class="card-text" style="left:302px">Our team at Bright Tutor may be small, but it's the exact size we need to make sure.</p>
  <p class="card-text" style="left:511px">Our team at Bright Tutor may be small, but it's the exact size we need to make sure.</p>
  <p class="card-text" style="left:719px">Our team at Bright Tutor may be small, but it's the exact size we need to make sure.</p>
  <p class="card-text" style="left:920px">Our team at Bright Tutor may be small, but it's the exact size we need to make sure.</p>
</section>

<section class="story">
  <div class="portrait"><div role="img" aria-label="Portrait of the foundation's namesake seated on a red sofa"></div></div>
  <h2 class="section-title abs" style="left:459px;top:1651px">Our Story</h2>
  <div class="rule abs" style="left:459px;top:1690px;width:118px"></div>
  <div class="body-copy abs" style="left:459px;top:1718px;width:642px;line-height:26px">
    <p>Marisol Avendano was a significant contributor to the beginning of Lark and Co. Properties. As one of the company's first employees, her plan was to work as an Administrative Assistant while she finished her undergraduate degree in Business Administration at Bayfield University. With plans to graduate in December of 2016, she couldn't wait to begin her real estate career, since she had just obtained her Real Estate license in 2014.</p>
    <p>However, on January 23rd, 2015, she was heading home from the Grand Opening party for Lark and Co. Properties when she was struck by a drunk driver and killed at the scene.</p>
  </div>
</section>

<section class="newsletter">
  <svg class="abs" style="left:125px;top:74px" width="170" height="112" viewBox="0 0 170 112"><path d="M85 0l85 32-85 32L0 32z" fill="#fff"/><path d="M38 50v30c0 14 94 14 94 0V50L85 68z" fill="#fff"/><path d="M152 38v44" stroke="#fff" stroke-width="3"/><rect x="146" y="82" width="12" height="20" fill="#fff"/></svg>
  <h2>Academic scholarships to high school students</h2>
  <p>The Marisol Avendano foundation will work to make a difference by not only offering scholarships and internships for future agents but by taking a stand against drinking and driving, an issue.</p>
  <span class="email-field">Email Address</span>
  <span class="btn-subscribe">SUBSCRIBE NOW</span>
</section>

<footer class="site-footer">
  <div class="footer-map" role="img" aria-label="Soft map background of the region"></div>
  <div class="footer-brand">Marisol<br>Avendano<small>FOUNDATION</small></div>

  <div class="footer-col abs" style="left:333px;top:54px">
    <h3>QUICK LINKS</h3><div class="rule"></div>
    <ul class="quick-links"><li>› Home</li><li>› Courses</li><li>› Features</li><li>› Events</li><li>› Scholarships</li><li>› Contact Us</li></ul>
  </div>

  <div class="footer-col abs" style="left:513px;top:54px;width:260px;height:260px">
    <h3>CONTACT US</h3><div class="rule"></div>
    <div class="contact-row" style="top:58px"><span class="contact-icon"><svg width="14" height="18" viewBox="0 0 14 18"><path d="M7 1a6 6 0 0 1 6 6c0 4-6 10-6 10S1 11 1 7a6 6 0 0 1 6-6z" fill="none" stroke="#4b1d6e" stroke-width="1.8"/><circle cx="7" cy="7" r="2" fill="#4b1d6e"/></svg></span><div><div class="label">MARISOL AVENDANO FOUNDATION,</div><div class="value">48 W. Willowbend<br>210 Larkfield, AZ 10987</div></div></div>
    <div class="contact-row" style="top:136px"><span class="contact-icon"><svg width="12" height="18" viewBox="0 0 12 18"><rect x="1" y="1" width="10" height="16" rx="2" fill="none" stroke="#4b1d6e" stroke-width="1.8"/><circle cx="6" cy="14" r="1" fill="#4b1d6e"/></svg></span><div><div class="label">PHONE:</div><div class="value">180 041 7720</div></div></div>
    <div class="contact-row" style="top:196px"><span class="contact-icon" style="background:#4b1d6e"><svg width="16" height="12" viewBox="0 0 16 12"><rect x="1" y="1" width="14" height="10" fill="none" stroke="#fff" stroke-width="1.5"/><path d="M1 1l7 6 7-6" fill="none" stroke="#fff" stroke-width="1.5"/></svg></span><div><div class="label">Mail:</div><div class="value">hello@marisolavendano.org</div></div></div>
  </div>

  <div class="footer-col abs" style="left:814px;top:54px">
    <h3>CONTACT FORM</h3><div class="rule"></div>
  </div>
  <span class="form-field" style="left:814px;top:109px;width:137px;height:35px">Name</span>
  <span class="form-field" style="left:962px;top:109px;width:137px;height:35px">Phone</span>
  <span class="form-field" style="left:814px;top:152px;width:285px;height:63px">Message</span>
  <span class="btn-solid abs" style="left:814px;top:230px;width:117px;height:38px;font-family:'Roboto',sans-serif;font-weight:500;font-size:12px">SEND MESSAGE</span>
</footer>

<div class="bottom-bar">
  <span class="copyright">Copyright © 2017 Marisol Avendano Foundation. All Rights Reserved.</span>
  <div class="bottom-social"><span></span><span></span><span></span><span></span><span></span></div>
</div>

</body>
</html>
```